Business Card - Tidal Lanes

Need Business Card design for company named Tidal Lanes. Software development focused mainly on Brindle Orvix & Zelt Apps. I've attached our logo with both a black and white background. Please add trademark symbol to logo when using.

```html
<!DOCTYPE html>
<html lang="en">
<head>
<meta charset="utf-8">
<title>Tidal Lanes – Business Card</title>
<link href="https://fonts.googleapis.com/css2?family=Open+Sans:wght@400;600;700&display=swap" rel="stylesheet">
<style>
  :root {
    --bg: #e9e9ee;
    --card: #050505;
    --red: #d71a16;
    --gold: #f4b400;
    --white: #ffffff;
  }
  * { margin: 0; padding: 0; box-sizing: border-box; }
  html, body { width: 1200px; height: 987px; overflow: hidden; background: var(--bg); }
  body { font-family: "Open Sans", Arial, sans-serif; position: relative; }

  .card {
    position: absolute;
    width: 760px; height: 434px;
    background: var(--card);
    border-radius: 34px;
    overflow: hidden;
    box-shadow: 0 10px 30px rgba(0,0,0,0.18);
  }
  .card--back { left: 400px; top: 30px; }
  .card--front { left: 40px; top: 520px; }

  .wordmark {
    position: absolute;
    display: flex; align-items: center; gap: 12px;
    color: var(--white);
    font-weight: 700;
    letter-spacing: -1px;
    white-space: nowrap;
  }
  .wordmark__dot { width: 18px; height: 18px; border-radius: 50%; background: var(--white); }
  .wordmark__tm { font-size: 0.35em; vertical-align: super; letter-spacing: 0; }

  .card--back .wordmark { font-size: 54px; left: 50%; top: 150px; transform: translateX(-50%); }
  .website {
    position: absolute; left: 0; right: 0; top: 250px;
    text-align: center; color: var(--white);
    font-size: 26px; letter-spacing: 3px;
  }

  .band { position: absolute; inset: 0; }

  .card--front .wordmark { font-size: 44px; left: 250px; top: 88px; }
  .person {
    position: absolute; left: 320px; top: 148px;
    color: var(--white); font-size: 26px; font-weight: 400;
    white-space: nowrap;
  }
  .person__name { color: var(--gold); font-weight: 700; }

  .contact {
    position: absolute; left: 40px; top: 285px;
    color: var(--white); font-size: 22px; line-height: 44px;
  }
  .contact__row { display: flex; align-items: center; gap: 10px; white-space: nowrap; }
  .contact__icon { width: 18px; height: 22px; fill: var(--white); }
  .contact__icon--call { width: 22px; margin-left: 10px; }
</style>
</head>
<body>

<section class="card card--back">
  <div class="wordmark"><span class="wordmark__dot"></span><span>Tidal Lanes<span class="wordmark__tm">™</span></span></div>
  <p class="website">www.tidallanes.com</p>
</section>

<section class="card card--front">
  <svg class="band" viewBox="0 0 760 434" width="760" height="434" aria-hidden="true">
    <path d="M0,200 Q520,200 720,434 L0,434 Z" fill="var(--red)"/>
    <path d="M0,190 Q532,190 738,434" fill="none" stroke="var(--gold)" stroke-width="4"/>
  </svg>

  <div class="wordmark"><span class="wordmark__dot"></span><span>Tidal Lanes<span class="wordmark__tm">™</span></span></div>
  <p class="person"><span class="person__name">Your Name,</span> Title</p>

  <div class="contact">
    <p class="contact__row">4120 Marsh Bend Rd, Oakridge, FL 33910</p>
    <p class="contact__row">
      <svg class="contact__icon" viewBox="0 0 18 22"><rect x="3" y="0" width="12" height="22" rx="2"/><rect x="5" y="3" width="8" height="10" fill="var(--red)"/></svg>
      555-204-7731
      <svg class="contact__icon contact__icon--call" viewBox="0 0 22 22"><path d="M4,2 L8,2 L10,7 L7,9 Q9,13 13,15 L15,12 L20,14 L20,18 Q20,20 18,20 Q4,18 2,4 Q2,2 4,2 Z"/></svg>
      555-318-4406
    </p>
  </div>
</section>

</body>
</html>
```